Home Remodeling company needs a business card design

we need a business card design for home remodeling company in hamilton county, indiana USA. we offers a wide range of construction services including whole house renovations, Design and Build Basements and Kitchen and Bathroom Remodeling . we would like to see designs for both site of business card that use the same color of the company logo and also including all information below :
1- Karim Feltous CEO / General Contractor
2- all company contacts Telephone numbers ( 1-888-DULOM-47 ) ( 317-555-0193) email address ( info@dulomhome.com) website ( www.dulomhome.com ) and social media logos (Facebook- twitter- google plus )
3- company logo
4- licensed . insured . bonded

```html
<!DOCTYPE html>
<html lang="en">
<head>
<meta charset="utf-8">
<title>Dulom Business Card</title>
<link rel="stylesheet" href="https://fonts.googleapis.com/css2?family=Merriweather:wght@700&family=Open+Sans:wght@400;800&display=swap">
<style>
  :root {
    --charcoal: #3d3c3a;
    --red: #c9252d;
    --white: #ffffff;
    --ink: #1e1e1e;
    --backdrop: #e9e7e4;
    --chip: #d6d4d1;
  }
  * { margin: 0; padding: 0; box-sizing: border-box; }
  html, body { width: 1189px; height: 1200px; overflow: hidden; }
  body { background: var(--backdrop); position: relative; font-family: "Open Sans", Arial, sans-serif; }

  .card {
    position: absolute; left: 140px; width: 918px; height: 523px;
    background: var(--white); overflow: hidden;
    box-shadow: 0 4px 14px rgba(0,0,0,.18);
  }
  .card--front { top: 47px; }
  .card--back { top: 623px; }

  .front__band-top { position: absolute; left: 0; top: 0; width: 100%; height: 226px; background: var(--charcoal); }
  .front__logo-pill {
    position: absolute; left: 0; top: 34px; width: 614px; height: 140px;
    background: var(--white); border-radius: 0 70px 70px 0;
    display: flex; align-items: center; padding-left: 46px;
  }
  .front__band-bottom { position: absolute; left: 0; bottom: 0; width: 100%; height: 24px; background: var(--charcoal); }

  .brand { display: flex; align-items: center; gap: 18px; }
  .brand__mark { width: 22px; height: 22px; background: var(--red); }
  .brand__name { font-weight: 800; color: var(--charcoal); letter-spacing: 4px; line-height: 1; }
  .front .brand__name { font-size: 78px; }
  .back .brand__name { font-size: 104px; }

  .person { position: absolute; left: 46px; top: 236px; }
  .person__name { font-family: "Merriweather", Georgia, serif; font-weight: 700; font-size: 33px; color: var(--red); line-height: 1.1; }
  .person__role { font-size: 24px; color: var(--ink); margin-top: 8px; }

  .contacts { position: absolute; left: 46px; top: 348px; list-style: none; }
  .contacts li { display: flex; align-items: center; height: 34.5px; font-size: 24px; color: var(--ink); }
  .contacts svg { width: 19px; height: 19px; margin-right: 27px; flex: none; }

  .social-pill {
    position: absolute; left: 511px; top: 333px; width: 407px; height: 139px;
    background: var(--charcoal); border-radius: 70px 0 0 70px;
    display: flex; align-items: center; padding-left: 72px; gap: 24px;
  }
  .social-pill__chip { width: 82px; height: 78px; border-radius: 9px; background: var(--chip); }

  .back__logo { position: absolute; left: 0; top: 180px; width: 100%; height: 128px; display: flex; justify-content: center; align-items: center; }
  .back__band-bottom { position: absolute; left: 0; bottom: 0; width: 100%; height: 36px; background: var(--charcoal); }
</style>
</head>
<body>

<section class="card card--front front">
  <div class="front__band-top"></div>
  <div class="front__logo-pill">
    <div class="brand"><span class="brand__mark"></span><span class="brand__name">DULOM</span></div>
  </div>

  <div class="person">
    <p class="person__name">Karim Feltous</p>
    <p class="person__role">CEO / General Contractor</p>
  </div>

  <ul class="contacts">
    <li>
      <svg viewBox="0 0 20 20"><rect width="20" height="20" fill="#c9252d"/><path d="M6 4l2.5 3-1.3 1.5a8 8 0 0 0 4.3 4.3L13 11.5l3 2.5-1.5 2C9 16 4 11 4 5.5z" fill="#fff"/></svg>
      1-888-DULOM-47
    </li>
    <li>
      <svg viewBox="0 0 20 20"><rect width="20" height="20" fill="#c9252d"/><path d="M6 4l2.5 3-1.3 1.5a8 8 0 0 0 4.3 4.3L13 11.5l3 2.5-1.5 2C9 16 4 11 4 5.5z" fill="#fff"/></svg>
      317-555-0193
    </li>
    <li>
      <svg viewBox="0 0 20 20"><rect width="20" height="20" fill="#c9252d"/><rect x="3.5" y="5.5" width="13" height="9" fill="none" stroke="#fff" stroke-width="1.5"/><path d="M3.5 5.5l6.5 5 6.5-5" fill="none" stroke="#fff" stroke-width="1.5"/></svg>
      info@dulomhome.com
    </li>
    <li>
      <svg viewBox="0 0 20 20"><rect width="20" height="20" fill="#c9252d"/><circle cx="10" cy="10" r="6" fill="none" stroke="#fff" stroke-width="1.5"/><path d="M4 10h12M10 4c-3 3-3 9 0 12M10 4c3 3 3 9 0 12" fill="none" stroke="#fff" stroke-width="1.2"/></svg>
      www.dulomhome.com
    </li>
  </ul>

  <div class="social-pill">
    <span class="social-pill__chip" role="img" aria-label="Social network link"></span>
    <span class="social-pill__chip" role="img" aria-label="Social network link"></span>
    <span class="social-pill__chip" role="img" aria-label="Social network link"></span>
  </div>

  <div class="front__band-bottom"></div>
</section>

<section class="card card--back back">
  <div class="back__logo">
    <div class="brand"><span class="brand__mark"></span><span class="brand__name">DULOM</span></div>
  </div>
  <div class="back__band-bottom"></div>
</section>

</body>
</html>
```